CREATE A KILLER WEBSITE DESIGN

We are a firearms training company that trains CIVILIANS (no police or military pictures - thank you!) to defend themselves and are looking for a killer design that's clean, easy to navigate and modern! We want the newest trends applied to this sight like a scrollable site so you can scroll down and see all the features. We are okay with tweaking the HTML but need the artistic design to look good. I'll provide a link to our current site along with a sight we really like so you can get an idea!

I'm supplying a PowerPoint Design we are going with from another designer so you can match the style to the new site.

PAGES: (Please use information from our current site. We like the information but just want a more polished look similar to the NWDPA site below but in our colors.)
Home - Long Form Scrolling Site. Top fold will be a video with a play button.
Harbor Institute - Seven Level Training Program Info Page That Will Contain A Video.
Contact Us - This will be a page that DOES NOT CONTAIN AN EMAIL ADDRESS. Just a contact us form
Meet The Trainer: Dennis Pollock

Our site:
https://www.brightmeadowskills.biz

Sights We Like:
https://www.nwdefenseplanners.com
https://quorvel.com
https://lindenplatecorp.com
https://www.velbrookgear.com

Target Market(s)

Men and women ages 21 to 100 years old

Industry/Entity Type

Self Defense

Number of Pages Required

5+ page

Font styles to use
Sans Serif

Colors
f26267

Requirements
Must have
• Clean and engaging. Use of colors that match our logo.
Should not have
• Poor design quality

```html
<!DOCTYPE html>
<html lang="en">
<head>
<meta charset="utf-8">
<title>Harbor Institute — Brightmeadow Skills</title>
<link href="https://fonts.googleapis.com/css2?family=Audiowide&family=Lato:wght@400;700&family=Roboto:wght@400;500;700&display=swap" rel="stylesheet">
<style>
:root{
  --black:#000;
  --ink:#0a0a0b;
  --red:#d8001f;
  --red-soft:#f26267;
  --white:#fff;
  --grey:#c9c9c9;
  --lv1:#8bab4a;
  --lv2:#2f8fd6;
  --lv3:#8a7591;
  --lv4:#1cb394;
  --lv5:#e85466;
  --lv6:#f3a23a;
  --lv7:#2b2f8c;
}
*{margin:0;padding:0;box-sizing:border-box}
html,body{width:1200px;height:3805px;overflow:hidden;background:var(--black)}
body{position:relative;font-family:"Lato",sans-serif;color:var(--white)}
.abs{position:absolute}
.display{font-family:"Audiowide",sans-serif;letter-spacing:1px}
.nav a,.foot-nav a{font-family:"Roboto",sans-serif;color:var(--white);text-decoration:none;font-size:12px;font-weight:500;letter-spacing:.3px;position:absolute}
.btn{position:absolute;background:var(--red);color:var(--white);font-family:"Roboto",sans-serif;font-weight:700;font-size:16px;border-radius:30px;display:flex;align-items:center;justify-content:center}

/* header */
.header{position:absolute;left:0;top:0;width:1200px;height:154px;background:var(--black)}
.phone-dot{position:absolute;left:111px;top:14px;width:38px;height:38px;border-radius:50%;background:var(--red);display:flex;align-items:center;justify-content:center}
.phone-num{left:170px;top:22px;font-family:"Roboto",sans-serif;font-weight:700;font-size:17px}
.rule{position:absolute;height:1px;background:#555}
.vrule{position:absolute;width:1px;background:#555}
.nav .active{color:var(--red)}
.nav .active::after{content:"";position:absolute;left:-6px;right:-6px;bottom:-9px;height:2px;background:var(--red)}
.social{position:absolute;top:16px;width:38px;height:38px;border-radius:50%;background:var(--red)}
.brand{position:absolute;left:510px;top:28px;width:172px;text-align:center}
.brand .mark{width:40px;height:40px;background:var(--red);margin:0 auto 8px}
.brand .name{font-family:"Audiowide",sans-serif;font-size:17px;color:var(--white);line-height:1.1}

/* hero */
.hero{position:absolute;left:0;top:154px;width:1200px;height:600px}
.hero-media{position:absolute;inset:0;background:linear-gradient(100deg,#2a2d31 0%,#3f4448 30%,#5a5049 50%,#3a4146 72%,#1f2a31 100%)}
.hero h1{position:absolute;left:538px;top:190px;font-family:"Audiowide",sans-serif;font-size:34px;line-height:46px;font-weight:400;letter-spacing:1px}
.side-word{position:absolute;top:262px;width:14px;font-family:"Roboto",sans-serif;font-weight:700;font-size:12px;line-height:33px;text-align:center}
.play{position:absolute;left:34px;top:435px;width:118px;height:118px;border-radius:50%;background:rgba(120,120,120,.55);display:flex;align-items:center;justify-content:center}
.play .ring{width:86px;height:86px;border-radius:50%;background:rgba(216,0,31,.7);display:flex;align-items:center;justify-content:center}
.play .core{width:58px;height:58px;border-radius:50%;background:var(--red);display:flex;align-items:center;justify-content:center}

.title{position:absolute;left:0;width:1200px;text-align:center;font-family:"Audiowide",sans-serif;font-size:34px;letter-spacing:1px}
.title span{color:var(--red)}
.title-bar{position:absolute;left:548px;width:104px;height:4px;background:var(--white)}

/* about */
.about{position:absolute;left:0;top:754px;width:1200px;height:886px;background:var(--black)}
.helmet{position:absolute;left:118px;top:236px;width:400px;height:518px;background:radial-gradient(circle at 45% 45%,#222 0%,#141414 60%,#000 100%);border-radius:48% 48% 10% 10%}
.bio{position:absolute;left:591px;top:224px;width:500px;font-size:17px;line-height:30px;color:#e8e8e8}
.seen-on{position:absolute;left:580px;top:580px;width:60px;transform:rotate(-90deg);transform-origin:center;font-family:"Audiowide",sans-serif;color:var(--red);font-size:15px;white-space:nowrap}
.outlet{position:absolute;top:635px;width:104px;height:56px;background:var(--white)}

/* levels */
.levels{position:absolute;left:0;top:1640px;width:1200px;height:969px;background:var(--ink)}
.lede{position:absolute;left:160px;top:188px;width:880px;text-align:center;font-size:17px;line-height:38px;color:#e8e8e8}
.lvl-num{position:absolute;font-family:"Audiowide",sans-serif;font-size:26px;line-height:1}
.lvl-name{position:absolute;font-size:17px;color:#e8e8e8;white-space:nowrap}

/* stories */
.stories{position:absolute;left:0;top:2609px;width:1200px;height:613px;background:var(--black)}
.story{position:absolute;top:220px;width:320px}
.story .q{font-family:"Lato",sans-serif;font-size:30px;color:var(--red);line-height:20px;font-weight:700}
.story p{font-size:16px;line-height:30px;color:#e8e8e8;margin-top:6px}
.who{display:flex;align-items:center;margin-top:12px}
.avatar{width:56px;height:56px;border-radius:50%;background:linear-gradient(#8d8d8d,#4b4b4b)}
.who span{margin-left:20px;font-family:"Audiowide",sans-serif;font-size:13px;color:var(--red)}

/* footer */
.footer{position:absolute;left:0;top:3222px;width:1200px;height:583px;background:var(--black)}
.foot-nav a{font-size:13px;top:118px}
.foot-nav i{position:absolute;top:118px;font-style:normal;font-size:13px;color:var(--white)}
.foot-brand{position:absolute;left:121px;top:188px;width:142px;text-align:center}
.foot-brand .mark{width:34px;height:34px;background:var(--red);margin:0 auto 8px}
.foot-brand .name{font-family:"Audiowide",sans-serif;font-size:15px;line-height:1.15}
.info{position:absolute;left:121px;font-family:"Roboto",sans-serif;font-size:12.5px;line-height:25px;display:flex}
.info svg{margin-right:12px;margin-top:6px;flex:none}
.info a{color:#4aa3e8;text-decoration:none}
.col-head{position:absolute;top:202px;font-family:"Roboto",sans-serif;font-weight:700;font-size:16px}
.field{position:absolute;background:var(--white);color:#888;font-family:"Roboto",sans-serif;font-size:12.5px;padding:14px 14px}
.follow a{position:absolute;left:929px;font-family:"Roboto",sans-serif;font-size:13px;color:var(--white);text-decoration:none}
.foot-badge{position:absolute;left:922px;top:396px;width:100px;text-align:center}
.foot-badge .mark{width:26px;height:26px;border-radius:50%;background:var(--white);margin:0 auto 6px}
.foot-badge .name{font-family:"Roboto",sans-serif;font-weight:700;font-size:10px}
.copy{position:absolute;left:0;top:526px;width:1200px;text-align:center;font-family:"Roboto",sans-serif;font-size:12.5px}
</style>
</head>
<body>

<header class="header">
  <div class="phone-dot"><svg width="16" height="16" viewBox="0 0 24 24"><path fill="#fff" d="M6.6 10.8a15.1 15.1 0 0 0 6.6 6.6l2.2-2.2a1 1 0 0 1 1-.25 11.4 11.4 0 0 0 3.6.57 1 1 0 0 1 1 1V20a1 1 0 0 1-1 1A17 17 0 0 1 3 4a1 1 0 0 1 1-1h3.5a1 1 0 0 1 1 1c0 1.25.2 2.45.57 3.57a1 1 0 0 1-.25 1z"/></svg></div>
  <div class="abs phone-num">904-555-0187</div>
  <div class="rule" style="left:110px;top:68px;width:355px"></div>
  <div class="rule" style="left:735px;top:68px;width:354px"></div>
  <div class="vrule" style="left:465px;top:0;height:133px"></div>
  <div class="vrule" style="left:735px;top:0;height:133px"></div>
  <nav class="nav">
    <a class="active" style="left:104px;top:96px">HOME</a>
    <a style="left:171px;top:96px">ABOUT US</a>
    <a style="left:263px;top:96px">LOST CERTIFICATE</a>
    <a style="left:788px;top:96px">TESTIMONIALS</a>
    <a style="left:910px;top:96px">UPCOMING CLASSES</a>
    <a style="left:1066px;top:96px">SHOP</a>
  </nav>
  <div class="brand"><div class="mark"></div><div class="name">Harbor Institute</div></div>
  <div class="social" style="left:915px" aria-label="Friendbook"></div>
  <div class="social" style="left:959px" aria-label="Snapgram"></div>
  <div class="social" style="left:1004px" aria-label="Chirper"></div>
  <div class="social" style="left:1048px" aria-label="Workline"></div>
</header>

<section class="hero">
  <div class="hero-media" role="img" aria-label="Video still: civilian student in ear protection aiming a pistol down an indoor firing range"></div>
  <div class="side-word" style="left:30px">P<br>R<br>E<br>V</div>
  <div class="side-word" style="left:1132px">N<br>E<br>X<br>T</div>
  <h1>YOUR LIFE MAY DEPEND<br>ON WHAT YOU LEARN<br>IN YOUR</h1>
  <div class="btn" style="left:540px;top:383px;width:221px;height:56px">HARBOR INSTITUTE</div>
  <div class="btn" style="left:780px;top:383px;width:222px;height:56px">GET TICKETS NOW</div>
  <div class="play"><div class="ring"><div class="core"><svg width="22" height="24" viewBox="0 0 22 24"><path fill="#fff" d="M2 1 21 12 2 23z"/></svg></div></div></div>
  <svg class="abs" style="left:0;top:555px" width="1200" height="45"><polygon points="0,0 320,12 1200,45 0,45" fill="#000"/><polygon points="0,0 620,30 0,45" fill="var(--red)"/></svg>
</section>

<section class="about">
  <h2 class="title" style="top:120px">ABOUT <span>DENNIS POLLOCK</span></h2>
  <div class="title-bar" style="top:174px"></div>
  <div class="helmet" role="img" aria-label="Large dark helmet emblem illustration"></div>
  <p class="bio">Dennis Pollock is a 3rd generation Jacksonville native and delighted to be a part of this great community.&nbsp; He is a true security expert with 25 years of experience in the security industry.&nbsp; He has appeared on KVR, TNB, WMX &amp; DLN news outlets.&nbsp; He has been Featured in numerous publications and has trained thousands to protect themselves and their homes from thugs and thieves. He is certified by both the NMC &amp; the NWDPA as a firearms instructor.&nbsp; He is also an NMC Range Safety Officer and Defensive Pistol Instructor.</p>
  <div class="btn" style="left:591px;top:517px;width:223px;height:56px">HARBOR INSTITUTE</div>
  <div class="seen-on">AS SEEN ON</div>
  <div class="outlet" style="left:636px"></div>
  <div class="outlet" style="left:750px"></div>
  <div class="outlet" style="left:865px"></div>
  <div class="outlet" style="left:979px"></div>
  <svg class="abs" style="left:0;top:835px" width="1200" height="51"><polygon points="1200,0 1200,51 540,51" fill="var(--red)"/></svg>
</section>

<section class="levels">
  <h2 class="title" style="top:96px">OUR 7 <span>LEVELS OF TRAINING</span></h2>
  <div class="title-bar" style="top:150px"></div>
  <p class="lede">Wanna hear something funny?&nbsp; Guess what the average person asks about a concealed weapons class?&nbsp; "How much is it and how long is it?"&nbsp; Can you believe it?&nbsp; We are talking about preparing you for life and death situations and the main concern is "How Fast" and "How Cheap?"&nbsp; WOW!</p>

  <svg class="abs" style="left:0;top:320px" width="1200" height="560" viewBox="0 0 1200 560" fill="none">
    <defs>
      <path id="pin" d="M0 14C-11 2-11-14 0-14S11 2 0 14Z"/>
    </defs>
    <g stroke-width="1">
      <line x1="140" y1="148" x2="140" y2="232" stroke="var(--lv1)"/>
      <line x1="415" y1="148" x2="415" y2="232" stroke="var(--lv2)"/>
      <line x1="680" y1="54" x2="680" y2="232" stroke="var(--lv3)"/>
      <line x1="983" y1="88" x2="983" y2="232" stroke="var(--lv4)"/>
      <line x1="983" y1="312" x2="983" y2="509" stroke="var(--lv5)"/>
      <line x1="680" y1="312" x2="680" y2="447" stroke="var(--lv6)"/>
      <line x1="415" y1="312" x2="415" y2="479" stroke="var(--lv7)"/>
    </g>
    <g stroke-width="16">
      <line x1="133" y1="232" x2="415" y2="232" stroke="var(--lv1)"/>
      <line x1="415" y1="232" x2="680" y2="232" stroke="var(--lv2)"/>
      <line x1="680" y1="232" x2="983" y2="232" stroke="var(--lv3)"/>
      <path d="M983 232H1025A40 40 0 0 1 1025 312H983" stroke="var(--lv4)"/>
      <line x1="983" y1="312" x2="680" y2="312" stroke="var(--lv5)"/>
      <line x1="680" y1="312" x2="415" y2="312" stroke="var(--lv6)"/>
      <line x1="415" y1="312" x2="133" y2="312" stroke="var(--lv7)"/>
    </g>
    <g stroke-width="4" fill="#1a1a1a">
      <circle cx="140" cy="232" r="9" stroke="var(--lv1)"/>
      <circle cx="415" cy="232" r="9" stroke="var(--lv2)"/>
      <circle cx="680" cy="232" r="9" stroke="var(--lv3)"/>
      <circle cx="983" cy="232" r="9" stroke="var(--lv4)"/>
      <circle cx="983" cy="312" r="9" stroke="var(--lv5)"/>
      <circle cx="680" cy="312" r="9" stroke="var(--lv6)"/>
      <circle cx="415" cy="312" r="9" stroke="var(--lv7)"/>
    </g>
    <use href="#pin" x="140" y="134" fill="var(--lv1)"/><circle cx="140" cy="130" r="4" fill="#1a1a1a"/>
    <use href="#pin" x="415" y="134" fill="var(--lv2)"/><circle cx="415" cy="130" r="4" fill="#1a1a1a"/>
    <use href="#pin" x="680" y="40" fill="var(--lv3)"/><circle cx="680" cy="36" r="4" fill="#1a1a1a"/>
    <use href="#pin" x="983" y="74" fill="var(--lv4)"/><circle cx="983" cy="70" r="4" fill="#1a1a1a"/>
    <use href="#pin" x="983" y="523" fill="var(--lv5)"/><circle cx="983" cy="519" r="4" fill="#1a1a1a"/>
    <use href="#pin" x="680" y="461" fill="var(--lv6)"/><circle cx="680" cy="457" r="4" fill="#1a1a1a"/>
    <use href="#pin" x="415" y="493" fill="var(--lv7)"/><circle cx="415" cy="489" r="4" fill="#1a1a1a"/>
  </svg>

  <div class="lvl-num" style="left:202px;top:352px;color:var(--lv1)">01</div>
  <div class="lvl-name" style="left:64px;top:380px">Concealed Carry Class</div>
  <div class="lvl-num" style="right:810px;top:452px;color:var(--lv2)">02</div>
  <div class="lvl-name" style="right:808px;top:486px">Dynamic Defensive Shooting</div>
  <div class="lvl-num" style="right:545px;top:356px;color:var(--lv3)">03</div>
  <div class="lvl-name" style="right:545px;top:384px">Fine Tuning Your Technique</div>
  <div class="lvl-num" style="right:244px;top:391px;color:var(--lv4)">04</div>
  <div class="lvl-name" style="right:244px;top:418px">Virtual Threat-lab</div>
  <div class="lvl-num" style="right:244px;top:799px;color:var(--lv5)">05</div>
  <div class="lvl-name" style="right:244px;top:828px">Tactical Skills &amp; Drills</div>
  <div class="lvl-num" style="right:545px;top:738px;color:var(--lv6)">06</div>
  <div class="lvl-name" style="right:545px;top:766px">Close Quarters Defense</div>
  <div class="lvl-num" style="right:808px;top:773px;color:var(--lv7)">07</div>
  <div class="lvl-name" style="right:808px;top:801px">Live Scenario Threat-lab</div>

  <svg class="abs" style="left:0;top:925px" width="1200" height="44"><polygon points="0,0 680,22 0,44" fill="var(--red)"/></svg>
</section>

<section class="stories">
  <h2 class="title" style="top:120px">OUR <span>SUCCESS STORIES</span></h2>
  <div class="title-bar" style="top:175px"></div>
  <article class="story" style="left:77px">
    <div class="q">“</div>
    <p>"I had never held a gun when I took the Brightmeadow Skills class and I'm hooked!&nbsp; I'm going all the way to level 7!&nbsp; Thank you Brightmeadow Skills!</p>
    <div class="who"><div class="avatar" role="img" aria-label="Student portrait"></div><span>MARISA K</span></div>
  </article>
  <article class="story" style="left:445px">
    <div class="q">“</div>
    <p>"I was mugged here in Jacksonville and lived in fear ever since.&nbsp; It stole my happiness and I became scared to go out.&nbsp; I'm a Level 4 student and I feel sorry for the next thug that tries me!"</p>
    <div class="who"><div class="avatar" role="img" aria-label="Student portrait"></div><span>LORETTA P.</span></div>
  </article>
  <article class="story" style="left:813px">
    <div class="q">“</div>
    <p>"I've been shooting for years and already had my concealed weapons license.&nbsp; My first class was a gun shop class and a waste of money.&nbsp; Dennis took the time to show me how to properly grip my gun and my shooting dramatically improved!</p>
    <div class="who"><div class="avatar" role="img" aria-label="Student portrait"></div><span>GRANT H.</span></div>
  </article>
</section>

<footer class="footer">
  <svg class="abs" style="left:0;top:0" width="1200" height="54"><polygon points="440,0 1200,0 1200,54" fill="var(--red)"/></svg>
  <div class="rule" style="left:110px;top:84px;width:978px"></div>
  <div class="rule" style="left:110px;top:155px;width:978px"></div>
  <nav class="foot-nav">
    <a style="left:138px">HOME</a><i style="left:203px">|</i>
    <a style="left:234px">ABOUT US</a><i style="left:326px">|</i>
    <a style="left:356px">HARBOR INSTITUTE</a><i style="left:514px">|</i>
    <a style="left:544px">TESTIMONIALS</a><i style="left:670px">|</i>
    <a style="left:699px">UPCOMING CLASSES</a><i style="left:858px">|</i>
    <a style="left:889px">SHOP</a><i style="left:952px">|</i>
    <a style="left:982px">VIDEOS</a>
  </nav>

  <div class="foot-brand"><div class="mark"></div><div class="name">Harbor Institute</div></div>
  <div class="info" style="top:322px">
    <svg width="12" height="14" viewBox="0 0 12 14"><path fill="#fff" d="M6 0a5 5 0 0 0-5 5c0 3.8 5 9 5 9s5-5.2 5-9a5 5 0 0 0-5-5zm0 7a2 2 0 1 1 0-4 2 2 0 0 1 0 4z"/></svg>
    <div>P.O. Box 4120<br>Cedar Bluff, Fl 32099</div>
  </div>
  <div class="info" style="top:392px">
    <svg width="13" height="13" viewBox="0 0 24 24"><path fill="#fff" d="M6.6 10.8a15.1 15.1 0 0 0 6.6 6.6l2.2-2.2a1 1 0 0 1 1-.25 11.4 11.4 0 0 0 3.6.57 1 1 0 0 1 1 1V20a1 1 0 0 1-1 1A17 17 0 0 1 3 4a1 1 0 0 1 1-1h3.5a1 1 0 0 1 1 1c0 1.25.2 2.45.57 3.57a1 1 0 0 1-.25 1z"/></svg>
    <div>904-555-0187</div>
  </div>
  <div class="info" style="top:428px">
    <svg width="16" height="12" viewBox="0 0 16 12"><rect width="16" height="12" rx="1" fill="#fff"/><path d="M1 1l7 5 7-5" stroke="#000" stroke-width="1.4" fill="none"/></svg>
    <a>hello@brightmeadowskills.biz</a>
  </div>

  <div class="vrule" style="left:387px;top:185px;height:273px"></div>
  <div class="vrule" style="left:894px;top:185px;height:273px"></div>

  <div class="col-head" style="left:429px">CONTACT US</div>
  <div class="field" style="left:433px;top:247px;width:203px;height:41px">First Name</div>
  <div class="field" style="left:647px;top:247px;width:204px;height:41px">Last Name</div>
  <div class="field" style="left:433px;top:300px;width:203px;height:42px">Email</div>
  <div class="field" style="left:647px;top:300px;width:204px;height:42px">Phone</div>
  <div class="field" style="left:433px;top:355px;width:418px;height:85px">Message</div>
  <svg class="abs" style="left:766px;top:394px" width="85" height="46"><polygon points="85,0 85,46 0,46" fill="var(--red)"/><path d="M70 22 58 30l4 1 1 5 3-4 4 2z" fill="#fff"/></svg>

  <div class="col-head" style="left:927px">FOLLOW US</div>
  <div class="follow">
    <a style="top:246px">Friendbook</a>
    <a style="top:271px">Snapgram</a>
    <a style="top:296px">Chirper</a>
    <a style="top:321px">Workline</a>
    <a style="top:348px">Viewtube</a>
  </div>
  <div class="foot-badge"><div class="mark"></div><div class="name">BRIGHTMEADOW SKILLS</div></div>

  <div class="rule" style="left:110px;top:483px;width:978px;background:#333"></div>
  <div class="copy">© Copyrights 2021 Brightmeadow Skills &nbsp;&nbsp;|&nbsp;&nbsp; All Rights Reserved</div>
</footer>

</body>
</html>
```